South Florida Real Estate Brokerage Business

The name is LAKE VORISSA REAL ESTATE.
The company is a Real estate realty based in Miami.
Is targeted to Latin American clients.
Must express luxury, and efficiency.
Target clients for properties around 250k to a million +.
Vorissa means Royal in Latin.
Should communicate safety and knowledge of the product and transaction with a tech edge.

The web design needs to be a Social tool, with Friendloop and other media integration of some sort. Needs to have a Show case place, a Search place (MLS listings) with maps and filters.
Needs to reflect luxury but also mixed with a social edge capable of engaging clients or transition them to communicate with the page.
Include the logo from the uploaded files, feel free to change the color or font per webdesign.
This is a Front en design, layout and graphics.
Possible future programming if approved.
I can receive Quotes for the Code part.

Spanish and English speakers living in Latin America and Canada looking for apartments and houses to buy.

Business

• Search area.
Neighbourhood area.
Could be a blog or news area.
Client registration.
Social Plugin
• Social linking to networks.
Log in with friendloop account.
Friendloop Like.

```html
<!DOCTYPE html>
<html lang="en">
<head>
<meta charset="utf-8">
<title>Lake Vorissa Real Estate</title>
<link rel="stylesheet" href="https://fonts.googleapis.com/css2?family=Cinzel:wght@400&family=PT+Sans:wght@400;700&display=swap">
<style>
:root{
  --gold:#c8ad6b;
  --gold-dark:#a88d48;
  --gold-line:#d2bd86;
  --brown:#7a5c0a;
  --olive:#8a6a08;
  --ink:#222;
  --text:#3a3a3a;
  --muted:#8a8a8a;
  --border:#a8a8a8;
  --orange-top:#ffc93a;
  --orange-bot:#f29a00;
  --white:#fff;
  --ph-map:#c9d6e6;
  --ph-photo:#b9bcb4;
  --ph-photo-tint:#b4c0b2;
  --ph-photo-grey:#b3b3b3;
  --ph-post:#9fae8c;
}
*{box-sizing:border-box;margin:0;padding:0}
html,body{width:1200px;height:1200px;overflow:hidden;background:var(--white)}
body{position:relative;font-family:"PT Sans",Arial,sans-serif;color:var(--ink)}
.abs{position:absolute}
.top-rule{left:0;top:0;width:1200px;height:3px;background:var(--gold)}

/* brand */
.brand{left:129px;top:14px;width:218px;text-align:center}
.brand-mark{width:60px;height:60px;background:var(--gold);margin:0 auto 22px}
.brand-name{font-family:"Cinzel",serif;font-size:24px;color:var(--ink);letter-spacing:1px;line-height:1;border-bottom:1px solid var(--gold-line);padding-bottom:6px}
.brand-sub{font-family:"Cinzel",serif;font-size:16px;color:var(--ink);letter-spacing:1px;margin-top:6px}

/* account */
.account-links{top:11px;font-size:14px;color:var(--ink)}
.account-links.active{color:var(--brown)}
.account-panel{left:604px;top:41px;width:463px;height:78px;background:var(--gold);border:1px solid var(--gold-dark)}
.account-pointer{left:922px;top:30px}
.field-label{font-size:14px;color:var(--ink)}
.field{height:22px;background:var(--white);border:1px solid #b9b9b9}
.btn{border-radius:12px;background:linear-gradient(var(--orange-top),var(--orange-bot));color:var(--white);font-size:15px;text-align:center;line-height:23px;box-shadow:0 1px 1px rgba(0,0,0,.25)}

/* nav */
.main-nav{top:138px;font-size:14px;color:var(--ink)}
.nav-band{left:0;top:162px;width:1200px;height:9px;background:var(--gold)}

/* quick search */
.section-title{font-size:19px;color:var(--brown)}
.map-area{background:var(--ph-map)}
.radio{width:15px;height:15px;border-radius:50%;border:1px solid #9a9a9a;background:radial-gradient(circle at 40% 35%,#fff,#d6d6d6)}
.opt{font-size:15px;color:var(--text)}
.select{height:21px;border:1px solid #b9c6d3;background:var(--white)}
.select svg{position:absolute;right:2px;top:2px}
.link{font-size:14px;color:var(--brown);text-decoration:underline}
.section-rule{left:0;top:385px;width:1200px;height:1px;background:var(--gold-line)}

/* showcase */
.card{top:408px;width:222px;height:272px;border:1px solid var(--border)}
.card-photo{height:217px}
.card-caption{text-align:center;font-size:15px;line-height:20px;color:var(--olive);padding-top:6px}
.tone-natural{background:var(--ph-photo)}
.tone-tint{background:var(--ph-photo-tint)}
.tone-grey{background:var(--ph-photo-grey)}

/* blog and news */
.frame-line{background:var(--gold-line)}
.post-photo{background:var(--ph-post)}
.post-title{font-size:16px;color:var(--ink)}
.post-meta{font-size:9px;letter-spacing:1.5px;color:var(--muted)}
.post-body{font-family:Arial,sans-serif;font-size:12.5px;line-height:19px;color:var(--muted)}
.post-body p{margin-bottom:12px}

.archive{left:848px;top:705px;width:223px;height:373px;border:1px solid var(--border);padding:7px 0 0 11px}
.archive h3{font-size:16px;font-weight:400;color:var(--brown);margin-bottom:7px}
.archive ul{list-style:none;padding-left:17px;font-size:14px;color:var(--ink)}
.archive li{height:28px}
.archive h3.second{margin-top:5px}

/* footer */
.footer{left:0;top:1099px;width:1200px;height:101px;background:var(--gold)}
.social-box{top:1105px;height:27px;background:var(--white);font-size:12px;color:var(--ink);display:flex;align-items:center;gap:8px;padding-left:7px}
.social-tile{width:17px;height:17px;border-radius:2px}
.like-btn{border:1px solid #9aa6c0;background:#eef1f7;padding:1px 5px;border-radius:2px;font-size:11px;color:#3b5490}
.copyright{left:979px;top:1114px;font-size:12px;color:var(--ink)}
</style>
</head>
<body>
<div class="abs top-rule"></div>

<header>
  <div class="abs brand">
    <div class="brand-mark"></div>
    <div class="brand-name">LAKE VORISSA</div>
    <div class="brand-sub">REAL ESTATE</div>
  </div>

  <a class="abs account-links" style="left:621px">Sign In</a>
  <a class="abs account-links" style="left:718px">Sign in with friendloop</a>
  <a class="abs account-links active" style="left:900px">Registration</a>

  <div class="abs account-panel"></div>
  <svg class="abs account-pointer" width="14" height="12" viewBox="0 0 14 12"><path d="M0 12 L7 0 L14 12 Z" fill="#c8ad6b" stroke="#a88d48"/><rect x="0" y="11" width="14" height="2" fill="#c8ad6b"/></svg>
  <form>
    <label class="abs field-label" style="left:621px;top:55px">Email</label>
    <div class="abs field" style="left:618px;top:77px;width:149px"></div>
    <label class="abs field-label" style="left:788px;top:55px">Password</label>
    <div class="abs field" style="left:785px;top:77px;width:149px"></div>
    <div class="abs btn" style="left:954px;top:76px;width:96px;height:23px">Register ›</div>
  </form>

  <nav>
    <a class="abs main-nav" style="left:491px">Home</a>
    <a class="abs main-nav" style="left:555px">Company</a>
    <a class="abs main-nav" style="left:642px">Associates</a>
    <a class="abs main-nav" style="left:732px">Search Properties</a>
    <a class="abs main-nav" style="left:864px">Marketing and Design</a>
    <a class="abs main-nav" style="left:1023px">Contact</a>
  </nav>
</header>
<div class="abs nav-band"></div>

<section class="quick-search">
  <h2 class="abs section-title" style="left:129px;top:185px;font-weight:400">QUICK SEARCH</h2>
  <div class="abs map-area" style="left:129px;top:227px;width:195px;height:148px;border:1px solid #c9c9c9" role="img" aria-label="Map of the search region"></div>

  <div class="abs radio" style="left:371px;top:227px"></div><span class="abs opt" style="left:398px;top:225px">BUY</span>
  <div class="abs radio" style="left:476px;top:227px"></div><span class="abs opt" style="left:505px;top:225px">SALE</span>
  <div class="abs radio" style="left:580px;top:227px"></div><span class="abs opt" style="left:609px;top:225px">FOR RENT</span>
  <div class="abs radio" style="left:711px;top:227px"></div><span class="abs opt" style="left:739px;top:225px">FOR RENT OUT</span>

  <span class="abs opt" style="left:371px;top:264px">PROPERTY TYPE</span>
  <div class="abs select" style="left:491px;top:263px;width:152px"><svg width="15" height="15"><rect width="15" height="15" fill="#dfe6ee" stroke="#9aa"/><path d="M4 6 L7.5 10 L11 6" fill="none" stroke="#445" stroke-width="1.6"/></svg></div>
  <span class="abs opt" style="left:702px;top:264px">PRICE&nbsp;&nbsp; Min</span>
  <div class="abs select" style="left:799px;top:263px;width:88px"><svg width="15" height="15"><rect width="15" height="15" fill="#dfe6ee" stroke="#9aa"/><path d="M4 6 L7.5 10 L11 6" fill="none" stroke="#445" stroke-width="1.6"/></svg></div>
  <span class="abs opt" style="left:928px;top:264px">MAX</span>
  <div class="abs select" style="left:970px;top:263px;width:100px"><svg width="15" height="15"><rect width="15" height="15" fill="#dfe6ee" stroke="#9aa"/><path d="M4 6 L7.5 10 L11 6" fill="none" stroke="#445" stroke-width="1.6"/></svg></div>

  <span class="abs opt" style="left:371px;top:305px">CITY NAME</span>
  <div class="abs select" style="left:491px;top:304px;width:152px"><svg width="15" height="15"><rect width="15" height="15" fill="#dfe6ee" stroke="#9aa"/><path d="M4 6 L7.5 10 L11 6" fill="none" stroke="#445" stroke-width="1.6"/></svg></div>
  <span class="abs opt" style="left:702px;top:305px">STATE</span>
  <div class="abs select" style="left:799px;top:304px;width:88px"><svg width="15" height="15"><rect width="15" height="15" fill="#dfe6ee" stroke="#9aa"/><path d="M4 6 L7.5 10 L11 6" fill="none" stroke="#445" stroke-width="1.6"/></svg></div>
  <span class="abs opt" style="left:908px;top:305px">ROOMS</span>
  <div class="abs select" style="left:970px;top:304px;width:100px"><svg width="15" height="15"><rect width="15" height="15" fill="#dfe6ee" stroke="#9aa"/><path d="M4 6 L7.5 10 L11 6" fill="none" stroke="#445" stroke-width="1.6"/></svg></div>

  <a class="abs link" style="left:371px;top:354px">Advance Search</a>
  <div class="abs btn" style="left:971px;top:350px;width:98px;height:24px">Search ›</div>
</section>
<div class="abs section-rule"></div>

<section class="showcase">
  <article class="abs card" style="left:129px"><div class="card-photo tone-natural" role="img" aria-label="Photo of a white colonial mansion"></div><p class="card-caption">Lorem Ipsum is simply<br>dummy text</p></article>
  <article class="abs card" style="left:370px"><div class="card-photo tone-tint" role="img" aria-label="Colour-toned photo of a white colonial mansion"></div><p class="card-caption">Lorem Ipsum is simply<br>dummy text</p></article>
  <article class="abs card" style="left:611px"><div class="card-photo tone-grey" role="img" aria-label="Black and white photo of a colonial mansion"></div><p class="card-caption">Lorem Ipsum is simply<br>dummy text</p></article>
  <article class="abs card" style="left:848px"><div class="card-photo tone-grey" role="img" aria-label="Black and white photo of a colonial mansion"></div><p class="card-caption">Lorem Ipsum is simply<br>dummy text</p></article>
</section>

<section class="posts">
  <div class="abs frame-line" style="left:139px;top:691px;width:1px;height:79px"></div>
  <div class="abs frame-line" style="left:129px;top:706px;width:692px;height:1px"></div>
  <div class="abs frame-line" style="left:806px;top:691px;width:1px;height:79px"></div>

  <h2 class="abs section-title" style="left:162px;top:724px;font-size:16px;font-weight:400">FROM THE BLOG</h2>
  <div class="abs post-photo" style="left:162px;top:757px;width:266px;height:121px" role="img" aria-label="Photo of a villa with pool among palm trees"></div>
  <h3 class="abs post-title" style="left:162px;top:883px;font-weight:400">Lorem Ipsum</h3>
  <span class="abs post-meta" style="left:171px;top:909px">SALE, RENT</span>
  <span class="abs post-meta" style="left:363px;top:909px">3 COMMENTS</span>
  <div class="abs post-body" style="left:162px;top:942px;width:262px">
    <p>Pellentesque habitant morbi tristique senectus et netus et malesuada fames ac turpis egestas. Vestibulum tortor.</p>
    <p>Pellentesque habitant morbi tristique senectus et netus et malesuada fames ac turpis egestas. Vestibulum tortor quam, feugiat vitae.</p>
  </div>

  <h2 class="abs section-title" style="left:483px;top:724px;font-size:16px;font-weight:400">NEWS</h2>
  <div class="abs post-photo" style="left:483px;top:757px;width:306px;height:121px" role="img" aria-label="Photo of a villa with pool among palm trees"></div>
  <h3 class="abs post-title" style="left:483px;top:883px;font-weight:400">Lorem Ipsum</h3>
  <div class="abs post-body" style="left:483px;top:907px;width:312px">
    <p>Pellentesque habitant morbi tristique senectus et netus et malesuada fames ac turpis egestas. Vestibulum tortor.</p>
    <p>Pellentesque habitant morbi tristique senectus et netus et malesuada fames ac turpis egestas. Vestibulum tortor quam, feugiat vitae.</p>
    <p>Pellentesque habitant morbi tristique senectus et netus et malesuada fames ac turpis egestas. Vestibulum tortor</p>
  </div>

  <aside class="abs archive">
    <h3>BLOG</h3>
    <ul><li>April (2012)&nbsp; (5)</li><li>March (2012)&nbsp; (5)</li><li>Feb (2012)&nbsp; (4)</li><li>Jan (2012)&nbsp; (8)</li><li>Dec (2011)&nbsp; (8)</li><li>Older Entries</li></ul>
    <h3 class="second">NEWS</h3>
    <ul><li>April (2012)&nbsp; (5)</li><li>March (2012)&nbsp; (5)</li><li>Feb (2012)&nbsp; (4)</li><li>Jan (2012)&nbsp; (8)</li></ul>
  </aside>
</section>

<footer>
  <div class="abs footer"></div>
  <div class="abs social-box" style="left:129px;width:217px">Connect with us
    <span class="social-tile" style="background:#3b5998"></span>
    <span class="social-tile" style="background:#4fa9d8"></span>
    <span class="social-tile" style="background:#f28c28"></span>
    <span class="social-tile" style="background:#f07a2a"></span>
  </div>
  <div class="abs social-box" style="left:359px;width:194px"><span class="like-btn">Like</span><span>347 others like this.</span></div>
  <p class="abs copyright">Copyright @ 2012</p>
</footer>
</body>
</html>
```